label design for soy candle

I am a start up making soy candles and other products involving scents.
On the label should be in writing : the scent, Handgemacht in der Schweiz, Sojakerze, my logo with the name Pellwick Candles on it. I will upload the currant label of my candles, but I want something more fashioned. The color of the label should be black with the scent written in gold, and the rest in white. Or maybe suggest something different, I am open to new designs. I am also open to change the logo, except the flower has to stay.
Sizes : square 60x60mm / round 50mm / rectangle 70x20mm ( for different jars )

```html
<!DOCTYPE html>
<html lang="en">
<head>
<meta charset="UTF-8">
<title>Pellwick Candles – Citrus Basil Label</title>
<link href="https://fonts.googleapis.com/css2?family=Bodoni+Moda:wght@500;600;700&display=swap" rel="stylesheet">
<style>
  :root {
    --backdrop: #0b0b0b;
    --marble-light: #8fd25a;
    --marble-mid: #4f9a2c;
    --marble-dark: #2e2623;
    --panel: #2f2624;
    --panel-deep: #231c1a;
    --gold: #d4a22a;
    --gold-light: #f1cf62;
    --leaf-green: #6cc23a;
  }
  * { margin: 0; padding: 0; box-sizing: border-box; }
  html, body {
    width: 1200px;
    height: 960px;
    overflow: hidden;
    background: var(--backdrop);
  }
  .canvas {
    position: relative;
    width: 1200px;
    height: 960px;
  }
  .label {
    position: absolute;
    left: 240px;
    top: 50px;
    width: 720px;
    height: 860px;
  }
  .label__pattern {
    position: absolute;
    inset: 0;
    background:
      radial-gradient(ellipse at 20% 15%, var(--marble-light) 0%, transparent 45%),
      radial-gradient(ellipse at 85% 80%, var(--marble-light) 0%, transparent 40%),
      radial-gradient(ellipse at 75% 10%, var(--marble-mid) 0%, transparent 50%),
      linear-gradient(135deg, var(--marble-mid) 0%, var(--marble-dark) 50%, var(--marble-mid) 100%);
  }
  .label__panel {
    position: absolute;
    left: 64px;
    right: 67px;
    top: 101px;
    bottom: 103px;
    background: linear-gradient(180deg, var(--panel) 0%, var(--panel-deep) 100%);
    border: 6px solid var(--gold);
    outline: 2px solid var(--gold-light);
    outline-offset: -9px;
    font-family: "Bodoni Moda", serif;
    text-align: center;
  }
  .brand {
    position: absolute;
    top: 48px;
    left: 0;
    right: 0;
  }
  .brand__mark {
    display: block;
    width: 62px;
    height: 62px;
    margin: 0 auto 22px;
    border-radius: 50%;
    background: var(--gold);
  }
  .brand__name {
    font-size: 30px;
    font-weight: 600;
    color: var(--gold);
    letter-spacing: 0.5px;
    text-transform: uppercase;
  }
  .scent {
    position: absolute;
    top: 296px;
    left: 0;
    right: 0;
  }
  .scent__name {
    font-size: 66px;
    font-weight: 700;
    color: var(--leaf-green);
    letter-spacing: -1px;
    line-height: 1;
  }
  .scent__rule {
    width: 348px;
    height: 3px;
    margin: 14px auto 22px;
    background: var(--leaf-green);
    border-radius: 2px;
  }
  .scent__type {
    font-size: 20px;
    font-weight: 600;
    color: var(--leaf-green);
    text-transform: uppercase;
  }
  .origin {
    position: absolute;
    bottom: 30px;
    left: 0;
    right: 0;
    color: var(--gold);
    font-weight: 600;
  }
  .origin__place {
    font-size: 21px;
    text-transform: uppercase;
    letter-spacing: -0.3px;
  }
  .origin__size {
    margin-top: 6px;
    font-size: 16px;
    text-transform: uppercase;
  }
  .origin__divider {
    display: inline-block;
    margin: 0 8px;
  }
</style>
</head>
<body>
  <main class="canvas">
    <section class="label">
      <div class="label__pattern" role="img" aria-label="Green and dark brown marbled swirl pattern framing the label"></div>
      <div class="label__panel">
        <div class="brand">
          <span class="brand__mark" aria-hidden="true"></span>
          <p class="brand__name">Pellwick Candles</p>
        </div>
        <div class="scent">
          <h1 class="scent__name">CITRUS BASIL</h1>
          <div class="scent__rule"></div>
          <p class="scent__type">Vegan Soy Wax Candle</p>
        </div>
        <div class="origin">
          <p class="origin__place">Hand Made in Switzerland</p>
          <p class="origin__size">8 oz<span class="origin__divider">|</span>237 ml</p>
        </div>
      </div>
    </section>
  </main>
</body>
</html>
```